Full re-design of visual identity

We have just re-designed our logo and would like to apply it on our folders, business cards, stationery, and etc... we are attaching new logo + the material we need to re-design... we will provide full corel draw files to help make job easier and also because lot of icons and artwork can be still used...

any doubts we are at your disposal. thanks in advance.

```html
<!DOCTYPE html>
<html lang="en">
<head>
<meta charset="utf-8">
<title>Corvale – Envelope Stationery</title>
<link rel="stylesheet" href="https://fonts.googleapis.com/css2?family=Open+Sans:wght@400;600;700&display=swap">
<style>
  :root {
    --canvas-bg: #f3f3f3;
    --paper: #ffffff;
    --paper-edge: #e4e4e4;
    --brand-orange: #ec8132;
    --brand-orange-deep: #c8512b;
    --brand-grey: #8a8a8a;
    --ink: #555555;
    --window-fill: #f6f6f6;
    --window-line: #d8d8d8;
  }
  * { box-sizing: border-box; margin: 0; padding: 0; }
  html, body {
    width: 1200px; height: 1000px; overflow: hidden;
    background: var(--canvas-bg);
    font-family: "Open Sans", Arial, sans-serif;
    color: var(--ink);
  }
  .canvas {
    position: relative; width: 1200px; height: 1000px;
  }
  .envelope {
    position: absolute; left: 220px; width: 760px; height: 380px;
    background: var(--paper);
    border: 1px solid var(--paper-edge);
    box-shadow: 0 6px 18px rgba(0,0,0,0.06);
    overflow: hidden;
  }
  .envelope--back { top: 70px; }
  .envelope--front { top: 530px; }

  .brand-name {
    font-weight: 700; color: var(--brand-grey);
    letter-spacing: -0.5px; line-height: 1;
    display: flex; align-items: center; gap: 6px;
  }
  .brand-name .brand-dot {
    width: 10px; height: 10px; border-radius: 50%;
    background: var(--brand-orange);
  }

  /* back of envelope */
  .envelope--back .brand-name {
    position: absolute; right: 42px; top: 34px; font-size: 30px;
  }
  .flap-band {
    position: absolute; left: 0; right: 30px; top: 84px; height: 12px;
    display: flex; gap: 6px;
  }
  .flap-band__grey { flex: 1; background: var(--brand-grey); border-radius: 6px 0 0 6px; }
  .flap-band__orange { width: 170px; background: var(--brand-orange); border-radius: 0 6px 6px 0; }

  /* front of envelope */
  .sender {
    position: absolute; left: 40px; top: 38px;
  }
  .sender .brand-name { font-size: 26px; }
  .sender__rule {
    width: 84px; height: 2px; background: var(--brand-orange); margin: 6px 0 10px;
  }
  .contact-list { list-style: none; font-size: 11px; line-height: 1.55; }
  .contact-list li { display: flex; align-items: flex-start; gap: 7px; }
  .contact-list svg { flex: none; margin-top: 3px; }

  .address-window {
    position: absolute; right: 40px; top: 46px; width: 300px; height: 130px;
    background: var(--window-fill);
    border: 1px solid var(--window-line);
    border-radius: 4px;
  }
  .brand-decoration {
    position: absolute; left: 190px; bottom: 0; width: 220px; height: 250px;
    border-radius: 110px 110px 0 0;
    background: linear-gradient(160deg, var(--brand-orange), var(--brand-orange-deep));
  }
</style>
</head>
<body>
<main class="canvas">

  <section class="envelope envelope--back" aria-label="Envelope back">
    <div class="brand-name">Corvale<span class="brand-dot"></span></div>
    <div class="flap-band">
      <span class="flap-band__grey"></span>
      <span class="flap-band__orange"></span>
    </div>
  </section>

  <section class="envelope envelope--front" aria-label="Envelope front">
    <div class="sender">
      <div class="brand-name">Corvale<span class="brand-dot"></span></div>
      <div class="sender__rule"></div>
      <ul class="contact-list">
        <li>
          <svg width="9" height="11" viewBox="0 0 10 12"><path d="M5 0a4 4 0 0 1 4 4c0 3-4 8-4 8S1 7 1 4a4 4 0 0 1 4-4z" fill="var(--brand-orange)"/></svg>
          <span>123 Main Street, Anytown,<br>Postal Code, Country</span>
        </li>
        <li>
          <svg width="9" height="9" viewBox="0 0 10 10"><path d="M2 0l2 2-1 2a6 6 0 0 0 3 3l2-1 2 2-2 2C4 10 0 6 0 2z" fill="var(--brand-orange)"/></svg>
          <span>555-1234-56</span>
        </li>
        <li>
          <svg width="10" height="9" viewBox="0 0 10 9"><rect x="0" y="0" width="10" height="9" rx="1" fill="var(--brand-orange)"/></svg>
          <span>555-1234-56</span>
        </li>
        <li>
          <svg width="10" height="8" viewBox="0 0 10 8"><rect width="10" height="8" rx="1" fill="var(--brand-orange)"/><path d="M0 1l5 4 5-4" stroke="#fff" fill="none"/></svg>
          <span>we@youraddress.com</span>
        </li>
        <li>
          <svg width="10" height="10" viewBox="0 0 10 10"><circle cx="5" cy="5" r="5" fill="var(--brand-orange)"/></svg>
          <span>www.yourwebsite.com</span>
        </li>
      </ul>
    </div>

    <div class="brand-decoration" role="img" aria-label="Orange brand graphic rising from the bottom edge"></div>

    <div class="address-window" aria-label="Address window"></div>
  </section>

</main>
</body>
</html>
```